Quick Straightforward Billboard Redesign

- Design billboard sized for 10 foot' x 36' foot width live area size and please include bleeds 6" around all sides
- Exact blue color match is imperative in headline, logo, phone number bubble or wherever used. C-83 / M-45 / Y-1 / K-0-
- What I hope to illustrate is that our company offers the best porch screening in the area area, in regards to quality, expertise, durability, storms proof, but we do not build screen porches.
- Current board is attached below from previous designer, and as you can see sizing was off, white space on edges make it appear to be sized incorrectly.
- I also attached my own little mock up idea well well if it helps, favorite image, logo, headline, etc and ideas perhaps on expanding or making this better?

Thanks so much!

Target Market(s)

Drivers and passengers, Southeastern NC, are of immense new construction and high end homes.

Industry/Entity Type

Construction

Colors
0054AA
0677BA
7BADD7
CADEEF
E8F1F8

Requirements
Must have
• Blue color matching
Nice to have
• Design spins or other thoughts on my little mock up

```html
<!DOCTYPE html>
<html lang="en">
<head>
<meta charset="utf-8">
<title>Pinecrest Porch Co. Billboard</title>
<link href="https://fonts.googleapis.com/css2?family=Bebas+Neue&family=Oswald:wght@400;600;700&display=swap" rel="stylesheet">
<style>
  :root {
    --brand-blue: #1570bd;
    --brand-blue-deep: #0054aa;
    --teal: #1b9aa6;
    --headline: #f4f5f7;
    --page: #ffffff;
    --sky: #cfe3f3;
    --lake: #8fb3cf;
    --lawn: #9cb85a;
    --patio: #d9d4c8;
  }
  * { margin: 0; padding: 0; box-sizing: border-box; }
  html, body {
    width: 1200px;
    height: 1031px;
    overflow: hidden;
    background: var(--page);
  }
  .billboard {
    position: absolute;
    left: 40px;
    top: 360px;
    width: 1120px;
    height: 313px;
    background: var(--brand-blue);
    overflow: hidden;
    box-shadow: 0 10px 18px rgba(0, 0, 0, 0.22);
    font-family: "Oswald", "Arial Narrow", sans-serif;
  }
  .porch-photo {
    position: absolute;
    left: 600px;
    top: 0;
    width: 520px;
    height: 244px;
    background:
      linear-gradient(180deg, #f2f2f0 0%, #f2f2f0 9%, var(--sky) 10%, #b9d3e8 30%, #7fa86a 40%, var(--lake) 46%, var(--lawn) 56%, var(--patio) 66%, #8c8275 82%, #cfc8bb 100%);
  }
  .photo-fade {
    position: absolute;
    left: 560px;
    top: 0;
    width: 240px;
    height: 244px;
    background: linear-gradient(90deg, var(--brand-blue) 0%, var(--brand-blue) 20%, rgba(21, 112, 189, 0) 100%);
  }
  .headline {
    color: var(--headline);
    text-transform: uppercase;
    font-weight: normal;
  }
  .headline span {
    position: absolute;
    left: 32px;
    line-height: 1;
    white-space: nowrap;
  }
  .headline .line-one {
    top: 25px;
    font-family: "Bebas Neue", "Oswald", sans-serif;
    font-size: 99px;
  }
  .headline .line-two {
    top: 101px;
    font-family: "Bebas Neue", "Oswald", sans-serif;
    font-size: 92px;
  }
  .headline .tagline {
    top: 172px;
    font-family: "Oswald", "Arial Narrow", sans-serif;
    font-weight: 400;
    font-size: 62px;
  }
  .bands {
    position: absolute;
    left: 0;
    top: 0;
    width: 1120px;
    height: 313px;
  }
  .company-name {
    position: absolute;
    left: 340px;
    top: 262px;
    width: 320px;
    text-align: center;
    color: var(--brand-blue-deep);
    font-weight: 600;
    font-size: 37px;
    line-height: 1;
    white-space: nowrap;
  }
  .phone {
    position: absolute;
    left: 790px;
    top: 253px;
    display: flex;
    align-items: center;
    gap: 8px;
    color: #ffffff;
  }
  .phone-icon { width: 32px; height: 32px; margin-top: 6px; }
  .phone-number {
    font-weight: 700;
    font-size: 46px;
    line-height: 1;
    white-space: nowrap;
  }
</style>
</head>
<body>
  <section class="billboard">
    <div class="porch-photo" role="img" aria-label="Photo of a screened porch with wicker seating overlooking a lawn and lake"></div>
    <div class="photo-fade"></div>

    <h1 class="headline">
      <span class="line-one">Screen</span>
      <span class="line-two">Your Porch.</span>
      <span class="tagline">Built for the Coast.</span>
    </h1>

    <svg class="bands" viewBox="0 0 1120 313" aria-hidden="true">
      <defs>
        <linearGradient id="phoneBubble" x1="0" y1="0" x2="1" y2="0">
          <stop offset="0" stop-color="#1f7bc6"/>
          <stop offset="1" stop-color="#1b9aa6"/>
        </linearGradient>
      </defs>
      <path d="M151 313 C 200 270, 255 247, 380 245 L 1120 241 L 1120 313 Z" fill="#ffffff"/>
      <path d="M380 245 L 1120 241" stroke="#1b9aa6" stroke-width="2" fill="none"/>
      <path d="M661 313 C 700 274, 745 250, 830 247 L 1120 245 L 1120 313 Z" fill="url(#phoneBubble)"/>
    </svg>

    <div class="company-name">Pinecrest Porch Co.</div>

    <div class="phone">
      <svg class="phone-icon" viewBox="0 0 34 34" aria-hidden="true">
        <circle cx="17" cy="17" r="15" fill="none" stroke="#ffffff" stroke-width="3"/>
        <path d="M11.5 9.5 L14.5 9 L16 13 L14 14.5 C15 17 17 19 19.5 20 L21 18 L25 19.5 L24.5 22.5 C23.5 24 21.5 24.5 19.5 23.8 C15 22 12 19 10.2 14.5 C9.5 12.5 10 10.5 11.5 9.5 Z" fill="#ffffff"/>
      </svg>
      <span class="phone-number">910-555-0142</span>
    </div>
  </section>
</body>
</html>
```